Beautiful design for wordpress

I need a beautiful, colourful and feminine website. My business is called 'The Velvet Lantern', and I sell crystals, books, CD's, pendulums and other metaphysical items. I also provide Reiki (energy healing).
I want this design to be eye catching and inspire happiness and joy in those who see it. And I would love to see the use of the logo and its colours :)
Please add these on the web design: Home, About, Online store, Blog

Industry/Entity Type

Business

Requirements
Must have
• Colourful and playful, must use the logo somewhere, have the words on a menu saying 'Home, Blog, Online store and about' (or similar to those)And the design must stand out!
Should not have
• grey, brown and other boring colours.

```html
<!DOCTYPE html>
<html lang="en">
<head>
<meta charset="utf-8">
<title>The Velvet Lantern – Crystals &amp; Gifts</title>
<link rel="stylesheet" href="https://fonts.googleapis.com/css2?family=Gelasio:wght@400;700&family=Open+Sans:wght@400;600&display=swap">
<style>
:root{
  --cream:#f6f1d3;
  --orange:#f7941d;
  --orange-soft:#fba54a;
  --magenta:#f23ea9;
  --magenta-dark:#c8268a;
  --olive:#7d8a3c;
  --green-soft:#e4efc6;
  --green:#b5ca58;
  --ink:#333333;
  --text:#5a5a5a;
  --card:#f9f9f6;
  --line:#dddddd;
  --footer:#efefef;
  --serif:"Gelasio", Georgia, serif;
  --sans:"Open Sans", Arial, sans-serif;
}
*{box-sizing:border-box;margin:0;padding:0}
html,body{width:1200px;height:2161px;overflow:hidden}
body{position:relative;background:#fff;font-family:var(--serif);color:var(--ink)}
.abs{position:absolute}
.top-band{left:0;top:0;width:1200px;height:452px;background:var(--cream)}

.brand{left:158px;top:70px;display:flex;align-items:center;gap:10px}
.brand-dot{width:26px;height:26px;border-radius:50%;background:var(--magenta)}
.brand-name{font-family:var(--serif);font-size:26px;font-weight:700;color:var(--olive);line-height:1.1;width:150px}

.util-links{left:722px;top:27px;font-size:13px;color:var(--ink)}
.login{left:952px;top:23px;width:81px;height:25px;background:var(--orange);color:#fff;font-size:13px;font-weight:700;text-align:center;line-height:25px;border-radius:3px}
.search{left:716px;top:72px;width:314px;height:33px;background:#fff;border:1px solid #e4e0c4;border-radius:3px}
.search span{position:absolute;left:10px;top:8px;font-size:11px;color:#c9c9c9;font-family:var(--sans)}
.search-btn{right:3px;top:3px;width:81px;height:25px;background:#6d6d6d;color:#fff;font-size:13px;font-weight:700;text-align:center;line-height:25px;border-radius:3px}

.main-nav{left:523px;top:140px;height:44px;display:flex;font-size:17px}
.main-nav a{color:var(--ink);text-decoration:none;line-height:44px;padding:0 21px}
.main-nav a.active{background:var(--orange);color:#fff;width:107px;text-align:center;padding:0}

.hero{left:166px;top:184px;width:868px;height:415px;background:linear-gradient(100deg,#c2489a 0%,#d27ab2 28%,#8fbf9f 50%,#d9c2a4 68%,#8f5c8e 82%,#cdb69a 100%)}
.hero-arrow{top:377px}

.promos{left:166px;top:621px;width:868px;display:flex;gap:19px}
.promo{width:277px;height:143px;background:#fff;border:1px solid var(--line);display:flex;align-items:center;padding-left:28px;gap:16px}
.promo-img{width:82px;height:98px}
.promo-copy{font-size:22px;line-height:23px;color:var(--olive)}
.promo-copy b{display:block;color:var(--orange);font-weight:400}

.filter-bar{left:166px;top:781px;width:868px;height:59px;background:var(--magenta);color:#fff;font-size:16px}
.filter-label{top:19px}
.select{top:11px;height:36px;background:var(--magenta-dark);border:1px solid #e7a3cf;border-radius:3px;font-size:12px;padding:9px 10px}
.select svg{position:absolute;right:10px;top:12px}

.section-title{font-size:21px;color:var(--olive)}

.product{width:202px;height:254px;background:var(--card)}
.product-img{position:absolute;left:61px;top:14px;width:80px;height:112px;border-radius:6px}
.product-name{position:absolute;left:10px;top:132px;font-size:12.5px;color:var(--olive);line-height:21px}
.price{position:absolute;left:10px;top:172px;font-size:22px;color:var(--olive)}
.btn{position:absolute;top:207px;height:28px;background:var(--orange-soft);color:#fff;font-size:12px;text-align:center;line-height:28px;border-radius:3px}
.btn-cart{left:10px;width:72px}
.btn-buy{left:93px;width:72px}

.pager{top:1456px;width:24px;height:24px;border:1px solid #ccc;background:#fff;font-size:10px;text-align:center;line-height:22px;font-family:var(--sans)}
.pager.current{background:#333;color:#fff;border-color:#333}

.newsletter{left:166px;top:1510px;width:868px;height:107px;background:var(--green-soft);border-radius:3px}
.news-title{left:64px;top:36px;font-size:22px;color:var(--ink)}
.news-input{left:276px;top:33px;width:425px;height:42px;background:#fff;border:1px solid #dfe8c5;font-family:var(--sans);font-size:11px;color:#c5c5c5;padding:14px 8px}
.subscribe{left:726px;top:32px;width:128px;height:44px;background:var(--green);color:#fff;font-size:18px;text-align:center;line-height:44px;border-radius:3px}

.body-copy{font-family:var(--sans);font-size:12.5px;line-height:22px;color:var(--text)}

.avatar{left:687px;top:1714px;width:149px;height:149px;border-radius:50%;background:radial-gradient(circle at 50% 45%,#8a8a8a,#1c1c1c 70%)}
.person{left:846px;top:1782px;font-size:20px;color:#666}
.person-co{left:846px;top:1814px;font-size:12px;color:#666}
.quote-mark{left:676px;top:1862px;font-size:52px;color:#aaa;line-height:0.8}

.footer{left:0;top:2069px;width:1200px;height:92px;background:var(--footer)}
.footer-nav{left:170px;top:22px;font-size:12.5px;color:var(--ink);display:flex;gap:0}
.footer-nav span.sep{padding:0 20px}
.copyright{left:170px;top:51px;font-size:12.5px;color:var(--ink)}
.pay{top:34px;height:25px;width:45px;background:#fff;border:1px solid #ccc;border-radius:2px;font-family:var(--sans);font-size:9px;font-weight:600;color:#444;text-align:center;line-height:23px}
.social{top:32px;width:28px;height:28px;border-radius:50%;background:#555;color:#fff;font-family:var(--sans);font-size:12px;font-weight:600;text-align:center;line-height:28px}
</style>
</head>
<body>
<div class="abs top-band"></div>

<header>
  <div class="abs brand"><div class="brand-dot"></div><div class="brand-name">The Velvet Lantern</div></div>
  <div class="abs util-links">My Account / Help Desk / Track Order</div>
  <div class="abs login">Login</div>
  <div class="abs search"><span>Search</span><div class="abs search-btn">Search</div></div>
  <nav class="abs main-nav">
    <a class="active" href="#">Home</a><a href="#">About</a><a href="#">Online store</a><a href="#">Blog</a><a href="#">Contact us</a>
  </nav>
</header>

<section class="abs hero" role="img" aria-label="Photo of a pink flower with green and purple tumbled crystals on sand"></section>
<svg class="abs hero-arrow" style="left:186px" width="30" height="46" viewBox="0 0 30 46"><path d="M26 4 6 23l20 19" fill="none" stroke="#fff" stroke-width="6"/></svg>
<svg class="abs hero-arrow" style="left:990px" width="30" height="46" viewBox="0 0 30 46"><path d="M4 4l20 19L4 42" fill="none" stroke="#fff" stroke-width="6"/></svg>

<section class="abs promos">
  <div class="promo"><div class="promo-img" role="img" aria-label="Ring with yellow stone" style="background:radial-gradient(circle,#d7dd52,#c9ced6 70%)"></div><div class="promo-copy"><b>15 % Off</b>Our Stone<br>Collections</div></div>
  <div class="promo"><div class="promo-img" role="img" aria-label="Cookbook cover" style="background:linear-gradient(#f4f2ec,#d8d4c8)"></div><div class="promo-copy"><b>25 % Off</b>Our Book<br>Collections</div></div>
  <div class="promo"><div class="promo-img" role="img" aria-label="Music CD with case" style="background:linear-gradient(90deg,#3a6fb0,#e7a43a,#b85dab)"></div><div class="promo-copy"><b>20 % Off</b>Our CDs<br>Collections</div></div>
</section>

<section class="abs filter-bar">
  <div class="abs filter-label" style="left:18px">Categories</div>
  <div class="abs select" style="left:105px;width:286px">All<svg width="14" height="10" viewBox="0 0 14 10"><path d="M1 2l6 6 6-6" fill="none" stroke="#fff" stroke-width="2.5"/></svg></div>
  <div class="abs filter-label" style="left:651px">Sort By :</div>
  <div class="abs select" style="left:716px;width:119px">All<svg width="14" height="10" viewBox="0 0 14 10"><path d="M1 2l6 6 6-6" fill="none" stroke="#fff" stroke-width="2.5"/></svg></div>
</section>

<h2 class="abs section-title" style="left:166px;top:862px;font-weight:400">Featured Products</h2>

<main>
  <div class="abs product" style="left:166px;top:906px"><div class="product-img" role="img" aria-label="Blue crystal pendant" style="background:linear-gradient(#8fd3ec,#1f6fa5)"></div><div class="product-name">Energy Crystal Charm Set<br>(Pack of 12)</div><div class="price">£5.99</div><div class="btn btn-cart">Add to cart</div><div class="btn btn-buy">Buy Now</div></div>
  <div class="abs product" style="left:388px;top:906px"><div class="product-img" role="img" aria-label="Purple crystal ball pendant" style="background:radial-gradient(circle,#b04a8f,#6a1f57)"></div><div class="product-name">Energy Crystal Charm Set<br>(Pack of 12)</div><div class="price">£5.99</div><div class="btn btn-cart">Add to cart</div><div class="btn btn-buy">Buy Now</div></div>
  <div class="abs product" style="left:609px;top:906px"><div class="product-img" role="img" aria-label="Novel book cover" style="background:linear-gradient(#5b5a8a,#8ea05d)"></div><div class="product-name">Energy Crystal Charm Set<br>(Pack of 12)</div><div class="price">£5.99</div><div class="btn btn-cart">Add to cart</div><div class="btn btn-buy">Buy Now</div></div>
  <div class="abs product" style="left:831px;top:906px"><div class="product-img" role="img" aria-label="Music album cover" style="background:linear-gradient(135deg,#f2c322,#2fb3c4)"></div><div class="product-name">Energy Crystal Charm Set<br>(Pack of 12)</div><div class="price">£5.99</div><div class="btn btn-cart">Add to cart</div><div class="btn btn-buy">Buy Now</div></div>

  <div class="abs product" style="left:166px;top:1186px"><div class="product-img" role="img" aria-label="Audio CD set" style="background:linear-gradient(135deg,#1d3c6b,#4f87b8)"></div><div class="product-name">Energy Crystal Charm Set<br>(Pack of 12)</div><div class="price">£5.99</div><div class="btn btn-cart">Add to cart</div><div class="btn btn-buy">Buy Now</div></div>
  <div class="abs product" style="left:388px;top:1186px"><div class="product-img" role="img" aria-label="Orange faceted gemstone" style="background:radial-gradient(circle,#ffd23f,#e07a0c)"></div><div class="product-name">Energy Crystal Charm Set<br>(Pack of 12)</div><div class="price">£5.99</div><div class="btn btn-cart">Add to cart</div><div class="btn btn-buy">Buy Now</div></div>
  <div class="abs product" style="left:609px;top:1186px"><div class="product-img" role="img" aria-label="Rainbow crystal pendant" style="background:linear-gradient(#7b6fb6,#3e4d8e)"></div><div class="product-name">Energy Crystal Charm Set<br>(Pack of 12)</div><div class="price">£5.99</div><div class="btn btn-cart">Add to cart</div><div class="btn btn-buy">Buy Now</div></div>
  <div class="abs product" style="left:831px;top:1186px"><div class="product-img" role="img" aria-label="Colourful jewelled necklace" style="background:linear-gradient(135deg,#e84a8c,#f2c94c,#4bb3e0)"></div><div class="product-name">Energy Crystal Charm Set<br>(Pack of 12)</div><div class="price">£5.99</div><div class="btn btn-cart">Add to cart</div><div class="btn btn-buy">Buy Now</div></div>
</main>

<nav aria-label="Pages">
  <div class="abs pager" style="left:655px"><svg width="8" height="10" viewBox="0 0 8 10"><path d="M6 1 2 5l4 4" fill="none" stroke="#333" stroke-width="1.8"/></svg></div>
  <div class="abs pager" style="left:691px">1</div>
  <div class="abs pager" style="left:726px">2</div>
  <div class="abs pager" style="left:761px">3</div>
  <div class="abs pager current" style="left:795px">4</div>
  <div class="abs pager" style="left:831px">5</div>
  <div class="abs" style="left:868px;top:1462px;font-size:12px">....</div>
  <div class="abs pager" style="left:900px">15</div>
  <div class="abs pager" style="left:936px">30</div>
  <div class="abs pager" style="left:974px">45</div>
  <div class="abs pager" style="left:1011px"><svg width="8" height="10" viewBox="0 0 8 10"><path d="M2 1l4 4-4 4" fill="none" stroke="#333" stroke-width="1.8"/></svg></div>
</nav>

<section class="abs newsletter">
  <svg class="abs" style="left:10px;top:40px" width="40" height="27" viewBox="0 0 40 27"><rect x="1" y="1" width="38" height="25" fill="#b5ca58"/><path d="M1 1l19 14L39 1M1 26l14-12M39 26 25 14" fill="none" stroke="#e4efc6" stroke-width="2"/></svg>
  <div class="abs news-title">Get The NewsLetter</div>
  <div class="abs news-input">Enter The E-Mail</div>
  <div class="abs subscribe">Subscribe</div>
</section>

<section>
  <h2 class="abs section-title" style="left:166px;top:1644px;font-weight:400">About Us</h2>
  <p class="abs body-copy" style="left:166px;top:1722px;width:492px">Lorem Ipsum is simply dummy text of the printing and typesetting industry. Lorem Ipsum has been the industry's standard dummy text ever since the 1500s, when an unknown printer took a galley of type and scrambled it to make a type specimen book. It has survived not only five centuries, but also the leap into electronic typesetting, remaining essentially unchanged. It was popularised in the 1960s with the release of Letraset sheets containing Lorem Ipsum passages, and more recently with desktop publishing software</p>
  <p class="abs body-copy" style="left:166px;top:1899px;width:492px">Lorem Ipsum is simply dummy text of the printing and typesetting industry. Lorem Ipsum has been the industry's standard dummy text ever since the 1500s, when an unknown printer took a galley of type and scrambled it to make a type specimen book. It has survived not only five centuries, but also the leap into electronic typesetting, remaining essentially unchanged.</p>
</section>

<section>
  <h2 class="abs section-title" style="left:684px;top:1644px;font-weight:400">Testimonials</h2>
  <div class="abs avatar" role="img" aria-label="Portrait photo of the customer"></div>
  <div class="abs person">Owen Hartley</div>
  <div class="abs person-co">Company Name</div>
  <div class="abs quote-mark">&ldquo;</div>
  <p class="abs body-copy" style="left:687px;top:1900px;width:350px">Lorem Ipsum is simply dummy text of the printing and typesetting industry. Lorem Ipsum has been the industry's standard dummy text ever since the 1500s, when an unknown printer took a galley of type and scrambled it to make a type specimen book.</p>
</section>

<footer class="abs footer">
  <div class="abs footer-nav"><span>Home</span><span class="sep">|</span><span>About</span><span class="sep">|</span><span>Online store</span><span class="sep">|</span><span>Blog</span><span class="sep">|</span><span>Contact us</span></div>
  <div class="abs copyright">© 2014 Company Name ,All Rights Reserved</div>
  <div class="abs pay" style="left:642px">Quilra</div>
  <div class="abs pay" style="left:692px">Cardora</div>
  <div class="abs pay" style="left:742px">Tovix</div>
  <div class="abs pay" style="left:792px">Penwick</div>
  <div class="abs social" style="left:866px" aria-label="Vidnest">V</div>
  <div class="abs social" style="left:901px" aria-label="Feedline">F</div>
  <div class="abs social" style="left:935px" aria-label="Chirpa">C</div>
  <div class="abs social" style="left:970px" aria-label="Circlo">O</div>
  <div class="abs social" style="left:1004px" aria-label="Worknet">W</div>
</footer>
</body>
</html>
```